Velvet Dice Night Age Verification Landing Page

To create a visually appealing design for the landing page of the adult game "Velvet Dice Night" that confirms the visitor's age.
The design should have a simple and visually appealing look that focuses on two buttons labeled "Yes" and "No". The purpose of the page is to confirm that the visitor is 18 years of age or older before accessing the game's content. Responsive design that works well on desktop and mobile devices. The final output should be delivered in PSD, AI, or Sketch format, along with any necessary images or assets.
I have also attached examples.

```html
<!DOCTYPE html>
<html lang="en">
<head>
<meta charset="UTF-8">
<title>Velvet Dice Night – Age Verification</title>
<link href="https://fonts.googleapis.com/css2?family=Great+Vibes&family=Montserrat:wght@400;500&display=swap" rel="stylesheet">
<style>
  :root {
    --bg-dark: #23262d;
    --bg-mid: #363a43;
    --photo-warm: #5a4640;
    --panel-purple: #4a2b72;
    --accent-blue: #4a9ad0;
    --accent-violet: #8c52e6;
    --accent-sky: #8cc8f0;
    --white: #ffffff;
    --brand-violet: #a55bd2;
    --line-grey: rgba(255,255,255,0.35);
  }
  * { box-sizing: border-box; margin: 0; padding: 0; }
  html, body { width: 1200px; height: 600px; overflow: hidden; background: var(--bg-dark); }
  .page {
    position: relative; width: 1200px; height: 600px; overflow: hidden;
    font-family: "Montserrat", sans-serif; color: var(--white);
  }
  .hero-photo {
    position: absolute; inset: 0;
    background:
      radial-gradient(ellipse 220px 320px at 530px 300px, rgba(90,70,64,0.55), transparent 70%),
      radial-gradient(ellipse 240px 330px at 1000px 230px, rgba(90,70,64,0.35), transparent 70%),
      linear-gradient(180deg, var(--bg-mid) 0%, var(--bg-dark) 100%);
  }
  .brand {
    position: absolute; left: 72px; top: 42px;
    display: flex; align-items: center; gap: 10px;
    font-size: 20px; font-weight: 500; color: var(--brand-violet);
  }
  .brand-dot { width: 14px; height: 14px; border-radius: 50%; background: var(--white); }
  .music-toggle {
    position: absolute; left: 1095px; top: 38px; width: 35px; height: 35px;
    border: 1px solid var(--white); border-radius: 6px;
    display: flex; align-items: center; justify-content: center;
  }
  .popup-shapes { position: absolute; inset: 0; }
  .popup-title {
    position: absolute; left: 366px; width: 467px; top: 198px;
    text-align: center; font-family: "Great Vibes", cursive;
    font-size: 60px; line-height: 1; color: var(--white);
  }
  .popup-question {
    position: absolute; left: 366px; width: 467px; top: 286px;
    text-align: center; font-size: 13px; letter-spacing: 0.3px;
  }
  .popup-actions { position: absolute; left: 523px; top: 322px; display: flex; gap: 4px; }
  .popup-button {
    width: 75px; height: 31px; background: var(--white); color: #222;
    border: none; font-family: "Montserrat", sans-serif; font-size: 11px;
    display: flex; align-items: center; justify-content: center;
  }
  .remember {
    position: absolute; left: 558px; top: 373px;
    display: flex; align-items: center; gap: 5px; font-size: 8.5px; font-weight: 500;
  }
  .remember-box { width: 8px; height: 8px; border-radius: 2px; background: #cfcfd6; }
</style>
</head>
<body>
<main class="page">
  <div class="hero-photo" role="img" aria-label="Blurred background photo of a laughing woman in a knit scarf and leather trousers"></div>

  <div class="brand"><span class="brand-dot"></span>Velvet Dice Night</div>

  <div class="music-toggle" aria-label="Toggle music">
    <svg width="18" height="18" viewBox="0 0 18 18" fill="none" stroke="#fff" stroke-width="1.6">
      <path d="M6 13V4l9-2v9"/>
      <circle cx="4" cy="13" r="2" fill="#fff"/>
      <circle cx="13" cy="11" r="2" fill="#fff"/>
    </svg>
  </div>

  <svg class="popup-shapes" width="1200" height="600" viewBox="0 0 1200 600">
    <path d="M366 173 H833 A22 22 0 0 1 855 195 V403 A22 22 0 0 1 833 425 H366 Z" fill="var(--accent-blue)"/>
    <polygon points="666,418 695,490 777,418" fill="var(--accent-blue)"/>
    <rect x="366" y="173" width="467" height="245" fill="var(--panel-purple)"/>
    <polygon points="674,417 698,474 763,417" fill="var(--panel-purple)"/>
    <rect x="377.5" y="186.5" width="442" height="219" fill="none" stroke="#fff" stroke-width="1.3" stroke-dasharray="1.5 3"/>
    <g stroke="var(--line-grey)" stroke-width="0.7">
      <line x1="364" y1="436" x2="660" y2="436"/>
      <line x1="364" y1="440" x2="660" y2="440"/>
      <line x1="364" y1="444" x2="660" y2="444"/>
      <line x1="364" y1="448" x2="660" y2="448"/>
      <line x1="364" y1="452" x2="660" y2="452"/>
    </g>
    <line x1="364" y1="459" x2="660" y2="459" stroke="var(--accent-violet)" stroke-width="1"/>
    <rect x="426" y="167" width="6" height="6" fill="#fff" transform="rotate(45 429 170)"/>
    <rect x="593" y="157" width="14" height="14" fill="var(--accent-violet)" transform="rotate(45 600 164)"/>
    <rect x="777" y="164" width="8" height="8" fill="var(--accent-sky)" transform="rotate(45 781 168)"/>
    <rect x="358" y="279" width="14" height="14" fill="var(--accent-violet)" transform="rotate(45 365 286)"/>
    <rect x="840" y="272" width="8" height="8" fill="#fff" transform="rotate(45 844 276)"/>
    <rect x="508" y="417" width="12" height="12" fill="var(--accent-violet)" transform="rotate(45 514 423)"/>
  </svg>

  <h1 class="popup-title">Midnight Play</h1>
  <p class="popup-question">Are you over 18 Years of age?</p>
  <div class="popup-actions">
    <span class="popup-button">YES</span>
    <span class="popup-button">NO</span>
  </div>
  <div class="remember"><span class="remember-box"></span>Remember Me?</div>
</main>
</body>
</html>
```